AUTO SPAREPART DISTRIBUTOR BUSINESS CARD

Our company need a business card design. We are a distributor and importer of car spareparts for VORN and PELTARO car model. We would like the design with White color back ground and attractive color for the fonts and looks clean, simple and attractive.
We provide the company information and the brand logo (VORN, PELTARO, ZUM, 738) should be put on the business card.

Thank you

Target Market(s)

Auto spareparts retailer shop and supplier.

Industry/Entity Type

Business

Contact Information for Business Card

The front side of the business card only contain company informations, and the back side may be put the brand logo (VORN, PELTARO, ZUM AND 738).

Requirements
Must have
• On the back side ( the brand logo) position , should have a transparency world map picture ( i uploaded the world map picture sample ).
• Also, need to put some words of " AUTO PARTS DISTRIBUTOR " (may be put on any appropriate place).

```html
<!DOCTYPE html>
<html lang="en">
<head>
<meta charset="utf-8">
<title>ZUM Business Card</title>
<link rel="stylesheet" href="https://fonts.googleapis.com/css2?family=Lato:wght@300;400&display=swap">
<style>
  :root {
    --page: #f1f1f1;
    --card: #ffffff;
    --green: #6a9e3e;
    --green-light: #a3cf45;
    --green-pale: #e4f0d2;
    --grey-band: #d4d4d4;
    --ink: #222222;
    --muted: #8a8a8a;
    --navy: #1d3b7c;
    --red: #c3161d;
  }
  * { margin: 0; padding: 0; box-sizing: border-box; }
  html, body { width: 1200px; height: 586px; overflow: hidden; }
  body {
    background: var(--page);
    font-family: "Lato", sans-serif;
    color: var(--ink);
    position: relative;
  }
  .card {
    position: absolute;
    top: 128px;
    width: 500px;
    height: 301px;
    background: var(--card);
    overflow: hidden;
    box-shadow: 0 2px 6px rgba(0,0,0,0.08);
  }
  .card--front { left: 86px; }
  .card--back { left: 606px; }

  /* front */
  .front-wordmark {
    position: absolute; left: 58px; top: 118px;
    display: flex; align-items: center; gap: 10px;
  }
  .front-wordmark .mark-square { width: 22px; height: 22px; background: var(--green); }
  .front-wordmark .name {
    font-weight: 300; font-size: 48px; letter-spacing: 2px; color: var(--ink); line-height: 1;
  }
  .divider {
    position: absolute; left: 214px; top: 64px; width: 2px; height: 160px;
    background: linear-gradient(to bottom, rgba(0,0,0,0), #222 50%, rgba(0,0,0,0));
  }
  .person { position: absolute; left: 282px; top: 48px; }
  .person .person-name { font-size: 16px; font-weight: 400; color: var(--green); letter-spacing: 0.5px; }
  .person .person-role { font-size: 12px; font-weight: 400; color: var(--muted); margin-top: 2px; }
  .contacts { position: absolute; left: 286px; top: 107px; list-style: none; }
  .contacts li {
    display: flex; align-items: center; height: 26px;
    font-size: 12px; font-weight: 400; color: var(--ink);
  }
  .contacts svg { width: 12px; height: 12px; margin-right: 8px; fill: var(--green); flex: none; }
  .address {
    position: absolute; left: 0; width: 418px; top: 256px;
    text-align: center; font-size: 12px; line-height: 16px; color: var(--green); font-weight: 400;
  }
  .edge-band--front {
    position: absolute; right: 0; top: 0; width: 86px; height: 301px;
    background: linear-gradient(to bottom, var(--green-pale), var(--grey-band) 45%, #c4c4c4);
    opacity: 0.75;
  }

  /* back */
  .edge-band--back {
    position: absolute; left: 0; top: 0; width: 88px; height: 301px;
    background: linear-gradient(to bottom, var(--green-pale), #d9ecbc 55%, var(--grey-band));
    opacity: 0.75;
  }
  .world-map {
    position: absolute; left: 34px; top: 36px; width: 432px; height: 212px;
    background: radial-gradient(ellipse at center, rgba(200,200,200,0.45), rgba(225,238,205,0.35) 60%, rgba(255,255,255,0) 80%);
  }
  .back-wordmark {
    position: absolute; left: 140px; top: 92px;
    display: flex; align-items: center; gap: 18px;
  }
  .back-wordmark .mark-square { width: 56px; height: 56px; background: var(--green); }
  .back-wordmark .name {
    font-weight: 300; font-size: 110px; line-height: 1; color: var(--ink); letter-spacing: 6px;
  }
  .brands {
    position: absolute; left: 0; width: 500px; top: 236px;
    display: flex; justify-content: center; gap: 26px;
  }
  .brands span { font-size: 12px; font-weight: 400; letter-spacing: 0.5px; }
  .brand--peltaro { color: var(--navy); }
  .brand--vorn { color: var(--red); }
  .brand--738 { color: var(--red); }
  .tagline {
    position: absolute; left: 0; width: 500px; top: 270px;
    text-align: center; font-size: 12px; letter-spacing: 3px; color: var(--green); font-weight: 400;
  }
</style>
</head>
<body>

<section class="card card--front">
  <div class="front-wordmark">
    <span class="mark-square"></span>
    <span class="name">ZUM</span>
  </div>
  <div class="divider"></div>

  <div class="person">
    <div class="person-name">RIAN HARTONO</div>
    <div class="person-role">Director</div>
  </div>

  <ul class="contacts">
    <li><svg viewBox="0 0 12 12"><circle cx="6" cy="6" r="6"/></svg>rian.hartono</li>
    <li><svg viewBox="0 0 12 12"><path d="M1 4c0-2 10-2 10 0v1H8V4H4v1H1zM3 6h6l2 4H1z"/></svg>+62-21-58230411</li>
    <li><svg viewBox="0 0 12 12"><path d="M3 1h6v3H3zM1 5h10v5H9V8H3v2H1zM3 9h6v2H3z"/></svg>+62-21-58230422</li>
    <li><svg viewBox="0 0 12 12"><path d="M3.5 0h5a1 1 0 0 1 1 1v10a1 1 0 0 1-1 1h-5a1 1 0 0 1-1-1V1a1 1 0 0 1 1-1zm.5 1.5v8h4v-8z"/></svg>+62-812730596</li>
    <li><svg viewBox="0 0 12 12"><path d="M0 2h12v1L6 7 0 3zM0 4.2l6 4 6-4V10H0z"/></svg>zum-trading@mailbox.id</li>
  </ul>

  <p class="address">Taman Permata 4, Blok C-07 No. B-15 ,<br>Kembangan, Jakarta Barat, Indonesia (11610)</p>

  <div class="edge-band--front"></div>
</section>

<section class="card card--back">
  <div class="edge-band--back"></div>
  <div class="world-map" role="img" aria-label="Faint dotted world map in light grey and pale green"></div>

  <div class="back-wordmark">
    <span class="mark-square"></span>
    <span class="name">ZUM</span>
  </div>

  <div class="brands">
    <span class="brand--peltaro">PELTARO</span>
    <span class="brand--vorn">VORN MOTORS</span>
    <span class="brand--738">738</span>
  </div>

  <p class="tagline">AUTO PARTS DISTRIBUTOR</p>
</section>

</body>
</html>
```